Business Cards - Brightpath Horizon

need to design unique business card for my mortgage business. I need to design credit card style business card for my business or any unique idea that you might have

Target Market(s)

Home Loan customers

Industry/Entity Type

Mortgage Brokerage

Contact Information for Business Card

please design credit card style or very unique style business card

Colors

Designer to choose colors to be used in the design.

Requirements
Must have
• Name
• position
• Phone number
• fax number
• email address
• website address
• social media address
• All above fields will be provided once design in finalised

```html
<!DOCTYPE html>
<html lang="en">
<head>
<meta charset="utf-8">
<title>Brightpath Horizon – Business Card</title>
<link rel="stylesheet" href="https://fonts.googleapis.com/css2?family=Share+Tech+Mono&family=Lora:wght@400;700&display=swap">
<style>
  :root {
    --page-bg: #e9e7e3;
    --card-deep: #14218f;
    --card-mid: #1d3fb3;
    --card-light: #2a64b8;
    --number-ink: #f2f4fa;
    --name-ink: #4fa6b6;
    --role-ink: #b88d5a;
    --contact-ink: #d9dfec;
    --brand-ink: #ffffff;
    --social-dot: rgba(255, 255, 255, 0.28);
  }
  * { box-sizing: border-box; margin: 0; padding: 0; }
  html, body {
    width: 1200px;
    height: 969px;
    overflow: hidden;
    background: var(--page-bg);
  }
  .canvas {
    position: relative;
    width: 1200px;
    height: 969px;
  }
  .card {
    position: absolute;
    left: 100px;
    top: 200px;
    width: 1000px;
    height: 570px;
    border-radius: 30px;
    overflow: hidden;
    background: linear-gradient(100deg, var(--card-deep) 0%, var(--card-mid) 45%, var(--card-light) 100%);
    box-shadow: 0 18px 40px rgba(20, 30, 80, 0.25);
    font-family: "Lora", serif;
  }
  .card-texture {
    position: absolute;
    right: 0;
    top: 0;
    width: 560px;
    height: 570px;
    background: radial-gradient(ellipse at 60% 45%, rgba(120, 170, 220, 0.28) 0%, rgba(120, 170, 220, 0) 70%);
  }
  .social-links {
    position: absolute;
    left: 52px;
    top: 70px;
    display: flex;
    gap: 8px;
  }
  .social-dot {
    width: 43px;
    height: 43px;
    border-radius: 50%;
    background: var(--social-dot);
  }
  .brand {
    position: absolute;
    right: 43px;
    top: 40px;
    width: 220px;
    text-align: right;
    color: var(--brand-ink);
    font-weight: 700;
    font-size: 34px;
    line-height: 1.1;
  }
  .card-number {
    position: absolute;
    left: 48px;
    top: 245px;
    color: var(--number-ink);
    font-family: "Share Tech Mono", monospace;
    font-size: 66px;
    letter-spacing: 6px;
    word-spacing: 18px;
    white-space: nowrap;
  }
  .holder {
    position: absolute;
    left: 53px;
    top: 460px;
  }
  .holder-name {
    color: var(--name-ink);
    font-weight: 700;
    font-size: 30px;
    letter-spacing: 1px;
  }
  .holder-role {
    color: var(--role-ink);
    font-weight: 700;
    font-size: 22px;
    letter-spacing: 1.5px;
    margin-top: 2px;
  }
  .contact {
    position: absolute;
    right: 50px;
    top: 438px;
    text-align: right;
    color: var(--contact-ink);
    font-size: 25px;
    line-height: 33px;
    letter-spacing: 1px;
  }
</style>
</head>
<body>
<div class="canvas">
  <div class="card">
    <div class="card-texture" role="img" aria-label="Faint tree texture across the card"></div>

    <div class="social-links" aria-label="Social media links">
      <span class="social-dot"></span>
      <span class="social-dot"></span>
      <span class="social-dot"></span>
      <span class="social-dot"></span>
    </div>

    <div class="brand">Brightpath Horizon</div>

    <div class="card-number">012 555 0147</div>

    <div class="holder">
      <div class="holder-name">DANIEL REYES</div>
      <div class="holder-role">CEO/FOUNDER</div>
    </div>

    <div class="contact">
      <div class="contact-phone">P. 555 214 7390</div>
      <div class="contact-email">hello@brightpath.com</div>
      <div class="contact-web">www.brightpath.com</div>
    </div>
  </div>
</div>
</body>
</html>
```